Business Card for a Dental Office

The design should communicate integrity, quality and reliability. We also want the card look elegant, simple, but still stand out, different from the traditional-dental-office business card.

Industry/Entity Type

Business

```html
<!DOCTYPE html>
<html lang="en">
<head>
<meta charset="utf-8">
<title>Harlow Dental Studio – Business Card</title>
<link rel="stylesheet" href="https://fonts.googleapis.com/css2?family=Oswald:wght@500&family=Open+Sans:wght@400;600&display=swap">
<style>
  :root {
    --page-bg: #5a5a5a;
    --card-black: #000000;
    --card-white: #ffffff;
    --gold: #d9c21c;
    --gold-deep: #b89a12;
    --text-dark: #3c3c3c;
    --text-light: #ffffff;
  }
  html, body {
    margin: 0;
    padding: 0;
    width: 1105px;
    height: 1200px;
    overflow: hidden;
    background: var(--page-bg);
  }
  .sheet {
    position: relative;
    width: 1105px;
    height: 1200px;
  }
  .card {
    position: absolute;
    left: 102px;
    width: 900px;
    height: 514px;
    overflow: hidden;
    font-family: "Open Sans", sans-serif;
  }
  .card--front { top: 56px; background: var(--card-white); }
  .card--back { top: 630px; background: var(--card-black); }

  .front-bands { position: absolute; inset: 0; }

  .holder { position: absolute; left: 41px; top: 36px; color: var(--text-light); }
  .holder__name { margin: 0; font-size: 31px; font-weight: 600; line-height: 1.1; }
  .holder__role { margin: 4px 0 0; font-size: 24px; font-weight: 400; }

  .brand {
    position: absolute;
    right: 41px;
    top: 268px;
    display: flex;
    align-items: center;
    gap: 14px;
  }
  .brand__square { width: 58px; height: 58px; background: var(--card-black); }
  .brand__text { text-align: left; }
  .brand__name {
    margin: 0;
    font-family: "Oswald", sans-serif;
    font-weight: 500;
    font-size: 38px;
    line-height: 1;
    color: var(--card-black);
  }
  .brand__tagline {
    margin: 3px 0 0;
    font-family: "Oswald", sans-serif;
    font-weight: 500;
    font-size: 17px;
    letter-spacing: 0.6px;
    color: var(--gold-deep);
  }

  .address {
    position: absolute;
    right: 452px;
    top: 384px;
    text-align: right;
    color: var(--text-dark);
    font-size: 24px;
    line-height: 31px;
    font-style: normal;
  }
  .contacts {
    position: absolute;
    right: 36px;
    top: 382px;
    margin: 0;
    padding: 0;
    list-style: none;
    color: var(--text-dark);
    font-size: 23px;
    line-height: 34px;
  }
  .contacts li { display: flex; justify-content: flex-end; align-items: center; gap: 14px; }
  .contacts svg { width: 22px; height: 22px; fill: var(--card-black); }

  .emblem-area {
    position: absolute;
    left: 60px;
    top: 70px;
    width: 380px;
    height: 380px;
    background: linear-gradient(135deg, #f2e23a, var(--gold) 55%, var(--gold-deep));
  }
  .back-brand { position: absolute; left: 509px; top: 362px; color: var(--gold); }
  .back-brand__name {
    margin: 0;
    font-family: "Oswald", sans-serif;
    font-weight: 500;
    font-size: 36px;
    line-height: 1;
  }
  .back-brand__tagline {
    margin: 4px 0 0;
    font-family: "Oswald", sans-serif;
    font-weight: 500;
    font-size: 15px;
    letter-spacing: 0.8px;
  }
  .back-brand__web { margin: 6px 0 0; font-size: 20px; letter-spacing: 3.5px; }
</style>
</head>
<body>
<main class="sheet">
  <section class="card card--front" aria-label="Card front">
    <svg class="front-bands" viewBox="0 0 900 514" width="900" height="514" aria-hidden="true">
      <polygon points="0,228 816,66 900,103 900,124 816,84 0,246" fill="var(--gold)"/>
      <polygon points="0,0 900,0 900,103 816,66 0,228" fill="var(--card-black)"/>
    </svg>

    <div class="holder">
      <p class="holder__name">Daniel Reyes</p>
      <p class="holder__role">CEO/Founder</p>
    </div>

    <div class="brand">
      <span class="brand__square" aria-hidden="true"></span>
      <div class="brand__text">
        <p class="brand__name">HARLOW DENTAL STUDIO</p>
        <p class="brand__tagline">YOUR SMILE IS YOUR GIFT TO OTHERS</p>
      </div>
    </div>

    <address class="address">
      1420 Larkspur Court<br>
      Juneau, Alaska 99801<br>
      www.harlowdental.example
    </address>

    <ul class="contacts">
      <li>555 210 4418
        <svg viewBox="0 0 24 24" aria-hidden="true"><path d="M6.6 10.8c1.4 2.8 3.8 5.1 6.6 6.6l2.2-2.2c.3-.3.7-.4 1-.2 1.1.4 2.3.6 3.6.6.6 0 1 .4 1 1V20c0 .6-.4 1-1 1C10.6 21 3 13.4 3 4c0-.6.4-1 1-1h3.5c.6 0 1 .4 1 1 0 1.3.2 2.5.6 3.6.1.3 0 .7-.2 1l-2.3 2.2z"/></svg>
      </li>
      <li>555 372 9065
        <svg viewBox="0 0 24 24" aria-hidden="true"><path d="M7 1h10a2 2 0 0 1 2 2v18a2 2 0 0 1-2 2H7a2 2 0 0 1-2-2V3a2 2 0 0 1 2-2zm0 3v14h10V4H7zm5 15.5a1.2 1.2 0 1 0 0 2.4 1.2 1.2 0 0 0 0-2.4z"/></svg>
      </li>
      <li>hello@harlowdental.example
        <svg viewBox="0 0 24 24" aria-hidden="true"><path d="M2 5h20v14H2V5zm2 2v.4l8 5.2 8-5.2V7H4z"/></svg>
      </li>
    </ul>
  </section>

  <section class="card card--back" aria-label="Card back">
    <div class="emblem-area" role="img" aria-label="Practice emblem area in gold"></div>
    <div class="back-brand">
      <p class="back-brand__name">HARLOW DENTAL STUDIO</p>
      <p class="back-brand__tagline">YOUR SMILE IS YOUR GIFT TO OTHERS</p>
      <p class="back-brand__web">www.harlowdental.example</p>
    </div>
  </section>
</main>
</body>
</html>
```